business card deign

Logo needs the following on it.
1. attached logo
2. Tagline - "If it keeps a drink cold or the party going...we do it!"
3. Name- Dalton Pikes, Founder and CPO
4. Address - 412 E. Carver Avenue, Ste 2207, Tampa, FL. 33917
5. Phone - 555.318.4726

```html
<!DOCTYPE html>
<html lang="en">
<head>
<meta charset="utf-8">
<title>Frostwell Co. Business Card</title>
<link href="https://fonts.googleapis.com/css2?family=Montserrat:wght@400;700&display=swap" rel="stylesheet">
<style>
  :root {
    --backdrop: #d9d6d3;
    --card-white: #ffffff;
    --card-black: #141414;
    --ink: #111111;
    --ink-soft: #2a2a2a;
    --mark-grey: #3a3a3a;
    --tag-grey: #bdbdbd;
    --emblem-dark: #1a1a1a;
    --emblem-back: #262626;
  }
  * { margin: 0; padding: 0; box-sizing: border-box; }
  html, body { width: 1200px; height: 786px; overflow: hidden; }
  body {
    background: var(--backdrop);
    position: relative;
    font-family: "Montserrat", sans-serif;
    color: var(--ink);
  }
  .card {
    position: absolute;
    top: 238px;
    width: 540px;
    height: 310px;
    box-shadow: 0 6px 18px rgba(0,0,0,0.18);
  }
  .card-front { left: 50px; background: var(--card-white); }
  .card-back { left: 610px; background: var(--card-black); }

  .emblem-area {
    position: absolute;
    left: 30px;
    top: 60px;
    width: 200px;
    height: 236px;
    background: linear-gradient(180deg, #2a2a2a, var(--emblem-dark));
  }
  .front-details {
    position: absolute;
    left: 270px;
    top: 40px;
  }
  .brand-name {
    font-weight: 700;
    font-size: 20px;
    color: var(--ink);
  }
  .person-name {
    margin-top: 20px;
    font-weight: 700;
    font-size: 17px;
  }
  .person-role, .address, .contact-line {
    font-size: 11px;
    color: var(--ink-soft);
  }
  .person-role { margin-top: 2px; }
  .address { margin-top: 18px; line-height: 1.45; }
  .contact-list { margin-top: 14px; list-style: none; }
  .contact-line {
    display: flex;
    align-items: center;
    gap: 8px;
    margin-bottom: 7px;
  }
  .contact-line svg { width: 11px; height: 11px; flex: none; }
  .icon-fill { fill: var(--ink); }
  .icon-line { fill: none; stroke: var(--ink); stroke-width: 2.4; }

  .back-emblem {
    position: absolute;
    left: 220px;
    top: 40px;
    width: 100px;
    height: 110px;
    background: linear-gradient(180deg, #333333, var(--emblem-back));
  }
  .back-mark {
    position: absolute;
    left: 0; right: 0;
    top: 168px;
    text-align: center;
    font-weight: 700;
    font-size: 20px;
    color: var(--mark-grey);
  }
  .tagline {
    position: absolute;
    left: 0; right: 0;
    top: 226px;
    text-align: center;
    font-size: 11px;
    color: var(--tag-grey);
  }
</style>
</head>
<body>
  <section class="card card-front">
    <div class="emblem-area" role="img" aria-label="Brand symbol area"></div>
    <div class="front-details">
      <div class="brand-name">Frostwell Co.</div>
      <div class="person-name">Dalton Pikes</div>
      <div class="person-role">Founder and CPO</div>
      <div class="address">412 E. Carver Avenue, Ste 2207,<br>Tampa, FL. 33917</div>
      <ul class="contact-list">
        <li class="contact-line">
          <svg viewBox="0 0 24 24"><path class="icon-fill" d="M6.6 10.8a15.1 15.1 0 0 0 6.6 6.6l2.2-2.2a1 1 0 0 1 1-.25 11.4 11.4 0 0 0 3.6.57 1 1 0 0 1 1 1V20a1 1 0 0 1-1 1A17 17 0 0 1 3 4a1 1 0 0 1 1-1h3.5a1 1 0 0 1 1 1c0 1.25.2 2.45.57 3.57a1 1 0 0 1-.25 1z"/></svg>
          <span>555.318.4726</span>
        </li>
        <li class="contact-line">
          <svg viewBox="0 0 24 24"><rect class="icon-line" x="2.5" y="5.5" width="19" height="13"/><path class="icon-line" d="M2.5 5.5l9.5 7.5 9.5-7.5"/></svg>
          <span>info@frostwell.com</span>
        </li>
        <li class="contact-line">
          <svg viewBox="0 0 24 24"><circle class="icon-line" cx="12" cy="12" r="9.5"/><path class="icon-line" d="M2.5 12h19M12 2.5c3 3 3 16 0 19M12 2.5c-3 3-3 16 0 19"/></svg>
          <span>www.frostwell.com</span>
        </li>
      </ul>
    </div>
  </section>

  <section class="card card-back">
    <div class="back-emblem" role="img" aria-label="Brand symbol area"></div>
    <div class="back-mark">Frostwell Co.</div>
    <p class="tagline">If it keeps a drink cold or the party going...we do it</p>
  </section>
</body>
</html>
```